World Wide News and Current Affairs website

We intends to start up a new website which deals on New and Current Affairs.
Attention Designers,
We want a home page design for this project. Our business is based in the United States. Our goal is to become a well known brand.
The website would consist of a category for News, Business and Tech.
The theme should be beautiful and attention seeking. The website would take bulk of it's news from the US, and Europe.
Designers can get inspiration from already existing new websites such as PWJ, KLV, DASKOLM.
All designs should be clean and easy to navigate.

```html
<!DOCTYPE html>
<html lang="en">
<head>
<meta charset="utf-8">
<title>Sample News — Home</title>
<link rel="stylesheet" href="https://fonts.googleapis.com/css2?family=Lato:wght@400;700;900&display=swap">
<style>
:root{
  --red:#e0061c;
  --red-dark:#c2041a;
  --red-line:#b9051b;
  --blue:#1a4f9c;
  --link:#2747a8;
  --ink:#222;
  --muted:#555;
  --beige:#ece6d8;
  --rule:#d9d9d9;
  --black:#111;
  --white:#fff;
  --page:#fafafa;
}
*{box-sizing:border-box;margin:0;padding:0}
html,body{width:1200px;height:1200px;overflow:hidden}
body{position:relative;background:var(--page);font-family:"Lato",Arial,sans-serif;color:var(--ink)}
.abs{position:absolute}

/* header */
.masthead{left:0;top:0;width:1200px;height:88px;background:linear-gradient(#ea0f24,var(--red))}
.brand{left:167px;top:32px;color:var(--white);font-weight:900;font-size:22px;letter-spacing:3px}
.account{left:920px;top:9px;color:var(--white);font-size:11px;display:flex;align-items:center;gap:6px}
.search-field{left:751px;top:43px;width:197px;height:29px;background:var(--white);border:1px solid #ddd;font-size:11px;color:#bbb;padding:8px 8px}
.search-btn{left:952px;top:43px;width:75px;height:29px;background:#efc7c4;color:var(--red-dark);font-size:12px;font-weight:700;text-align:center;line-height:29px}
.mainnav{left:0;top:88px;width:1200px;height:43px;background:linear-gradient(var(--red),var(--red-dark));box-shadow:0 2px 4px rgba(0,0,0,.15)}
.mainnav ul{position:absolute;left:171px;top:0;display:flex;list-style:none;height:43px}
.mainnav li{color:var(--white);font-size:12px;height:43px;line-height:43px;padding:0 24px;border-right:1px solid rgba(0,0,0,.15)}
.mainnav li.active{background:var(--white);color:var(--red);width:84px;padding:0;text-align:center}

/* breaking */
.breaking{left:171px;top:149px;width:856px;height:40px}
.breaking-label{left:0;top:0;width:176px;height:40px;background:var(--blue);color:var(--white);font-weight:900;font-size:12px;line-height:40px;padding-left:16px;clip-path:polygon(0 0,92% 0,100% 50%,92% 100%,0 100%)}
.ticker{left:180px;top:0;width:526px;height:40px;background:var(--beige);font-size:11px;line-height:40px;padding-left:14px;color:#444;white-space:nowrap;overflow:hidden}
.clock{left:745px;top:0;width:111px;height:40px;background:var(--blue);color:var(--white);font-size:11px;text-align:center;line-height:40px}

/* media placeholders */
.ph{position:absolute}
.lead-photo{left:171px;top:204px;width:514px;height:329px;background:linear-gradient(135deg,#cfd6e0,#eef1f5 50%,#9aa6b5)}
.lead-caption{left:171px;top:471px;width:514px;height:62px;background:rgba(20,20,20,.8);color:var(--white);padding:12px 14px}
.lead-caption h2{font-size:14px;font-weight:900}
.lead-caption p{font-size:10px;margin-top:6px}
.play{left:405px;top:323px}
.side-photo{left:699px;top:204px;width:328px;height:139px;background:linear-gradient(#1a2550,#7a3a4a 60%,#b0503a)}
.side-caption{left:716px;top:309px;color:var(--white);font-weight:700;font-size:13px}
.market-photo{left:699px;top:408px;width:328px;height:125px;background:linear-gradient(135deg,#0d2d78,#1f64c4 60%,#cfd8e8)}

/* section heads */
.sechead{height:37px;border-bottom:2px solid var(--red-line)}
.sechead .tag{display:inline-block;height:37px;line-height:37px;padding:0 10px;background:var(--red-line);color:var(--white);font-weight:700;font-size:12px;text-transform:uppercase}
.sechead.dark{border-bottom-color:#333}
.sechead.dark .tag{background:var(--black)}
.pager{position:absolute;right:2px;top:11px;color:var(--red);font-size:13px;font-weight:900;letter-spacing:6px}

.tabs{left:171px;top:548px;width:489px;height:37px;border-bottom:2px solid var(--red-line);display:flex;gap:3px}
.tabs span{height:35px;line-height:35px;padding:0 10px;background:var(--beige);font-size:12px;color:#555;font-weight:700}
.tabs span.on{background:var(--red-line);color:var(--white)}

.headlines{left:171px;top:597px;width:489px;list-style:none}
.headlines li{height:45px;display:flex;align-items:center;font-size:13px;color:var(--link);border-bottom:1px solid var(--rule)}
.headlines li.short{height:40px}
.headlines .flag{width:72px;height:27px;background:var(--blue);color:var(--white);font-size:10px;line-height:27px;padding-left:12px;margin-right:14px;clip-path:polygon(0 0,82% 0,100% 50%,82% 100%,0 100%)}

.card{width:203px}
.card .photo{width:203px;height:136px}
.card h3{font-size:12px;font-weight:400;margin-top:16px;text-transform:uppercase;color:#333}
.card ul{list-style:none;margin-top:8px}
.card li{font-size:11px;color:var(--link);height:26px;display:flex;align-items:center;gap:8px}
.card li svg{flex:none}
.crowd{background:linear-gradient(#1a2550,#7a3a4a 60%,#b0503a)}
.desk{background:linear-gradient(135deg,#cfd6e0,#eef1f5 50%,#9aa6b5)}

/* social */
.social{left:699px;top:603px;width:328px}
.social-row{height:45px;display:flex;align-items:center;font-size:11px;color:#444}
.social-mark{width:33px;height:33px;margin-right:12px}
.social-row .btn{margin-left:auto;background:var(--black);color:var(--white);font-size:11px;height:33px;line-height:33px;padding:0 18px}
.ad{left:720px;top:747px;width:287px;height:240px;background:#e3e3e3;color:#bbb;font-size:13px;text-align:center;line-height:240px}
.feature-photo{left:699px;top:1065px;width:328px;height:135px;background:linear-gradient(90deg,#0b2a7a,#1f4fd0 55%,#0b1a50)}
.feature-tag{left:700px;top:1088px;background:var(--blue);color:var(--white);font-size:9px;padding:5px 10px}
.feature-date{left:746px;top:1088px;background:rgba(0,0,0,.4);color:var(--white);font-size:9px;padding:5px 12px}
</style>
</head>
<body>

<header>
  <div class="abs masthead"></div>
  <div class="abs brand">SAMPLE NEWS</div>
  <div class="abs account">
    <svg width="14" height="12" viewBox="0 0 14 12"><circle cx="7" cy="4" r="3" fill="#fff"/><path d="M1 12c0-4 3-5 6-5s6 1 6 5z" fill="#fff"/></svg>
    Log In / Register
  </div>
  <div class="abs search-field">Search</div>
  <div class="abs search-btn">SEARCH</div>
  <nav class="abs mainnav">
    <ul>
      <li class="active">Home</li><li>News</li><li>Finance</li><li>Entertainment</li><li>Tech</li><li>Contact Us</li>
    </ul>
  </nav>
</header>

<section class="abs breaking">
  <div class="abs breaking-label">BREAKING NEWS ➡</div>
  <div class="abs ticker">Lorem ipsum dolor sit amet, consectetur adipiscing elit, sed do eiusmod tempor incididunt ut labore.</div>
  <div class="abs clock">GMT+2 07:50 AM</div>
</section>

<div class="ph lead-photo" role="img" aria-label="Lead story photo: office desk with keyboard, tablet and charts"></div>
<svg class="abs play" width="48" height="48" viewBox="0 0 48 48"><circle cx="24" cy="24" r="21" fill="rgba(0,0,0,.25)" stroke="#fff" stroke-width="3"/><path d="M19 14l14 10-14 10z" fill="#fff"/></svg>
<div class="abs lead-caption">
  <h2>Lorem Ipsum Dolor Sit Amet</h2>
  <p>Lorem ipsum dolor sit amet, consectetur adipiscing elit, sed do eiusmod.</p>
</div>

<div class="ph side-photo" role="img" aria-label="Concert crowd with raised hands before a lit stage"></div>
<div class="abs side-caption">Lorem Ipsum Dolor</div>

<div class="abs sechead" style="left:699px;top:357px;width:328px"><span class="tag">Market</span><span class="pager">‹›</span></div>
<div class="ph market-photo" role="img" aria-label="Stock market chart on a blue screen"></div>

<div class="abs tabs"><span class="on">LOREM IPSUM</span><span>LOREM IPSUM</span><span>LOREM IPSUM</span></div>

<ul class="abs headlines">
  <li><span class="flag">LOREM</span>Lorem ipsum dolor sit amet, consectetur adipiscing?</li>
  <li class="short">Lorem ipsum dolor sit amet, consectetur adipiscing.</li>
  <li class="short">Lorem ipsum dolor sit amet, consectetur adipiscing elit.</li>
  <li><span class="flag">LOREM</span>Lorem ipsum dolor sit amet, consectetur adipiscing?</li>
  <li class="short">Lorem ipsum dolor sit amet, consectetur.</li>
  <li class="short" style="border:0">Lorem ipsum dolor sit amet, consectetur adipiscing.</li>
</ul>

<div class="abs sechead" style="left:171px;top:844px;width:489px"><span class="tag">Lorem Ipsum</span><span class="pager">‹›</span></div>

<article class="abs card" style="left:171px;top:904px">
  <div class="photo crowd" role="img" aria-label="Concert crowd photo"></div>
  <h3>Lorem Ipsum Dolor Sit</h3>
  <ul>
    <li><svg width="9" height="8"><path d="M1 4l2.5 3L8 1" stroke="#444" stroke-width="1.5" fill="none"/></svg>Lorem ipsum dolor sit amet</li>
    <li><svg width="9" height="8"><path d="M1 4l2.5 3L8 1" stroke="#444" stroke-width="1.5" fill="none"/></svg>Consectetur adipiscing elit <svg width="9" height="7"><rect width="9" height="7" fill="#c00"/></svg></li>
    <li><svg width="9" height="8"><path d="M1 4l2.5 3L8 1" stroke="#444" stroke-width="1.5" fill="none"/></svg>Cras laoreet vel enim in iaculis</li>
    <li><svg width="9" height="8"><path d="M1 4l2.5 3L8 1" stroke="#444" stroke-width="1.5" fill="none"/></svg>Phasellus dignissim</li>
  </ul>
</article>

<article class="abs card" style="left:431px;top:904px">
  <div class="photo desk" role="img" aria-label="Office desk with devices photo"></div>
  <h3>Lorem Ipsum Dolor Sit</h3>
  <ul>
    <li><svg width="9" height="8"><path d="M1 4l2.5 3L8 1" stroke="#444" stroke-width="1.5" fill="none"/></svg>Lorem ipsum dolor sit amet <svg width="9" height="7"><rect width="9" height="7" fill="#c00"/></svg></li>
    <li><svg width="9" height="8"><path d="M1 4l2.5 3L8 1" stroke="#444" stroke-width="1.5" fill="none"/></svg>Consectetur adipiscing elit</li>
    <li><svg width="9" height="8"><path d="M1 4l2.5 3L8 1" stroke="#444" stroke-width="1.5" fill="none"/></svg>Cras laoreet vel enim in iaculis <svg width="9" height="7"><rect width="9" height="7" fill="#c00"/></svg></li>
    <li><svg width="9" height="8"><path d="M1 4l2.5 3L8 1" stroke="#444" stroke-width="1.5" fill="none"/></svg>Phasellus dignissim</li>
  </ul>
</article>

<div class="abs sechead dark" style="left:699px;top:548px;width:328px"><span class="tag">Social</span></div>
<div class="abs social">
  <div class="social-row"><span class="social-mark" style="background:#3b5a98"></span>78,695 Fans<span class="btn">Like</span></div>
  <div class="social-row"><span class="social-mark" style="background:#3d9be0"></span>295,651 Followers<span class="btn">Follow</span></div>
  <div class="social-row"><span class="social-mark" style="background:#c8312a"></span>1,057 Subscribers<span class="btn">Subscribe</span></div>
</div>

<div class="abs ad">336x280</div>

<div class="abs sechead dark" style="left:699px;top:1008px;width:328px"><span class="tag">Lorem Ipsum</span></div>
<div class="ph feature-photo" role="img" aria-label="Sports feature photo of a tennis player on a blue background"></div>
<div class="abs feature-tag">Lorem</div>
<div class="abs feature-date">03 Aug, 2014</div>

</body>
</html>
```